Business Cards Design for the electrical wholesaler: clean bold dynamic :)

We need a business card design that would follow our latest brand guidelines. As an electrical wholesaler we want to bring a fresh look and feel into the industry. The design should be clean bold and dynamic. It should come alive with the renewed energy of our green colour. Our grey colour should keep things balanced and complement the notion of maturity and responsibility. We employ Lato as a corporate font however are not bound by this font and we’re open to interpretation here.

Target Market(s)

Electrical contractors

Industry/Entity Type

Business

Contact Information for Business Card

Logo
Name & Surname: Halyna Dorosh
Job Title: Director of Marketing
Email: halya.dorosh@quillmail.example
Cell phone: XXX.XXX.XXXX
Address: 20517 - 87 Ave. Edmonton, AB, Canada. T6K 4N8
Business Phone: 780.555.0184
Website: www.brovix.example

Font styles to use
Other font styles liked:
• Lato

Requirements
Must have
• Logo & website
Nice to have
• Brand elements - some of them you may find in the attached Brand Guidelines (e.g. three lines on the background signifying "W")

```html
<!DOCTYPE html>
<html lang="en">
<head>
<meta charset="utf-8">
<title>Brovix Business Card</title>
<link href="https://fonts.googleapis.com/css2?family=Lato:wght@400;700&display=swap" rel="stylesheet">
<style>
  :root {
    --backdrop: #2a2a2a;
    --green: #80bd3c;
    --green-dark: #6fa92f;
    --grey: #4d4d4f;
    --grey-text: #4d4d4f;
    --paper: #f2f2f2;
    --white: #ffffff;
  }
  * { margin: 0; padding: 0; box-sizing: border-box; }
  html, body {
    width: 1200px; height: 960px; overflow: hidden;
    background: var(--backdrop);
    font-family: "Lato", Arial, sans-serif;
  }
  .canvas { position: relative; width: 1200px; height: 960px; }

  .card {
    position: absolute; width: 600px; height: 342px;
    border-radius: 22px; overflow: hidden;
  }
  .card-front { left: 314px; top: 113px; background: var(--paper); }
  .card-back { left: 311px; top: 472px; background: var(--green); }

  .brand-name {
    position: absolute; font-family: "Lato", Arial, sans-serif;
    font-weight: 400; letter-spacing: -1px; line-height: 1;
    display: flex; align-items: center; gap: 14px;
  }
  .brand-dot { display: inline-block; border-radius: 50%; }
  .card-front .brand-name { left: 54px; top: 48px; font-size: 56px; color: var(--grey-text); }
  .card-front .brand-dot { width: 34px; height: 34px; background: var(--green); }

  .contact-band {
    position: absolute; left: 0; top: 160px; width: 100%; height: 142px;
    background: var(--grey);
  }
  .person { position: absolute; left: 60px; top: 48px; }
  .person-name {
    font-size: 24px; font-weight: 700; color: var(--green);
    text-transform: uppercase; line-height: 1.05;
  }
  .person-title { font-size: 16px; color: var(--white); margin-top: 2px; }

  .contact-list {
    position: absolute; left: 326px; top: 25px; list-style: none;
  }
  .contact-list li {
    display: flex; align-items: center; height: 19px;
    font-size: 14.5px; color: var(--white);
  }
  .contact-list svg { width: 13px; height: 13px; margin-right: 10px; fill: var(--green); flex: none; }

  .address-band {
    position: absolute; left: 0; top: 302px; width: 100%; height: 40px;
    background: var(--green);
    font-size: 15px; color: var(--white);
    padding-left: 57px; line-height: 38px;
  }

  .card-back .brand-name {
    left: 0; right: 0; top: 145px; justify-content: center;
    font-size: 72px; color: var(--white);
  }
  .card-back .brand-dot { width: 44px; height: 44px; background: var(--white); }
  .back-web {
    position: absolute; left: 0; right: 0; top: 292px; text-align: center;
    font-size: 13px; letter-spacing: 3.4px; color: var(--white);
  }
</style>
</head>
<body>
<div class="canvas">

  <section class="card card-front">
    <div class="brand-name"><span class="brand-dot"></span>brovix</div>

    <div class="contact-band">
      <div class="person">
        <div class="person-name">Halyna Dorosh</div>
        <div class="person-title">CEO/FOUNDER</div>
      </div>
      <ul class="contact-list">
        <li>
          <svg viewBox="0 0 16 16" aria-hidden="true"><path d="M3.5 1.5l2.5 0 1.2 3.3-1.6 1.2c.9 1.9 2.4 3.4 4.3 4.3l1.2-1.6 3.3 1.2v2.5c0 .9-.7 1.6-1.6 1.6C6.8 14 2 9.2 2 3.1c0-.9.7-1.6 1.5-1.6z"/></svg>
          780.555.0184
        </li>
        <li>
          <svg viewBox="0 0 16 16" aria-hidden="true"><path d="M4.5 0h7c.8 0 1.5.7 1.5 1.5v13c0 .8-.7 1.5-1.5 1.5h-7C3.7 16 3 15.3 3 14.5v-13C3 .7 3.7 0 4.5 0zM5 2v10h6V2H5zm3 11a1 1 0 100 2 1 1 0 000-2z"/></svg>
          780.555.0127
        </li>
        <li>
          <svg viewBox="0 0 16 16" aria-hidden="true"><path d="M4 1h8v4H4zM1 6h14v7h-2v-3H3v3H1zM4 11h8v4H4z"/></svg>
          780.555.0193
        </li>
        <li>
          <svg viewBox="0 0 16 16" aria-hidden="true"><path d="M1 3h14v10H1zM2 4.2v.5l6 4 6-4v-.5z"/></svg>
          halya.dorosh@quillmail.example
        </li>
        <li>
          <svg viewBox="0 0 16 16" aria-hidden="true"><circle cx="8" cy="8" r="7"/><path d="M5 4c1 .5 1.5 1.5 1 2.5s.5 2 1.5 2 1 1.5.5 3M10 3c-.5 1 0 2 1 2.2" stroke="#4d4d4f" stroke-width="1.2" fill="none"/></svg>
          www.brovix.example
        </li>
      </ul>
    </div>

    <div class="address-band">20517 - 87 Ave. Edmonton, AB, Canada. T6K 4N8</div>
  </section>

  <section class="card card-back">
    <div class="brand-name"><span class="brand-dot"></span>brovix</div>
    <div class="back-web">www.brovix.example</div>
  </section>

</div>
</body>
</html>
```